German Headhunter/ HR Consultancy needs Business Cards Design

We need a business Card Design for our Company in Stuttgart. We are specialized as Headhunter/ HR Consultancy in Placement of specialist and managers in permanent employment. Please refer to our business logo.

```html
<!DOCTYPE html>
<html lang="en">
<head>
<meta charset="utf-8">
<title>Kernwerk Personalberatung – Business Card</title>
<link rel="stylesheet" href="https://fonts.googleapis.com/css2?family=Arimo:wght@400;700&display=swap">
<style>
  :root {
    --brand-blue: #3a55a6;
    --brand-blue-deep: #2f4893;
    --pattern-blue: #4762b0;
    --paper: #ffffff;
    --accent-grey: #9a9ca3;
    --text-light: #ffffff;
    --stage: #1d1d1f;
  }
  * { box-sizing: border-box; margin: 0; padding: 0; }
  html, body {
    width: 1200px; height: 900px; overflow: hidden;
    background: var(--stage);
    font-family: "Arimo", Arial, sans-serif;
  }
  .stage {
    width: 1200px; height: 900px;
    display: flex; align-items: center; justify-content: center; gap: 60px;
  }
  .card {
    position: relative;
    width: 525px; height: 300px;
    border-radius: 18px;
    overflow: hidden;
    background: var(--brand-blue);
    color: var(--text-light);
  }
  /* Front */
  .card-front .corner-shape { position: absolute; inset: 0; width: 100%; height: 100%; }
  .holder { position: absolute; left: 34px; top: 30px; }
  .holder-name {
    font-weight: 700; font-size: 25px; letter-spacing: 1px; text-transform: uppercase;
  }
  .holder-role { font-size: 15px; margin-top: 4px; }
  .contact {
    position: absolute; left: 34px; bottom: 34px;
    list-style: none; font-size: 13.5px; line-height: 1.5;
  }
  .contact li { display: flex; align-items: center; gap: 8px; }
  .contact .address { padding-left: 22px; }
  .contact svg { width: 14px; height: 14px; flex: none; fill: var(--text-light); }
  .brand-front {
    position: absolute; right: 34px; bottom: 62px;
    color: var(--brand-blue); font-weight: 700; text-align: left;
  }
  .brand-name { font-size: 26px; letter-spacing: 2px; text-transform: uppercase; display: flex; align-items: center; gap: 10px; }
  .brand-mark { width: 16px; height: 16px; background: currentColor; }
  .brand-sub { font-size: 11px; letter-spacing: 1.6px; text-transform: uppercase; margin-left: 26px; margin-top: 3px; }
  /* Back */
  .pattern-field {
    position: absolute; inset: 0;
    background: linear-gradient(135deg, var(--brand-blue-deep), var(--pattern-blue) 60%, var(--brand-blue));
  }
  .brand-back {
    position: absolute; left: 40px; bottom: 40px; color: var(--text-light); font-weight: 700;
  }
</style>
</head>
<body>
<main class="stage">
  <section class="card card-front" aria-label="Business card front">
    <svg class="corner-shape" viewBox="0 0 525 300" preserveAspectRatio="none" aria-hidden="true">
      <polygon points="245,150 525,110 525,300 260,300" fill="var(--accent-grey)"/>
      <polygon points="255,160 525,125 525,300 268,300" fill="var(--paper)"/>
    </svg>
    <div class="holder">
      <h1 class="holder-name">Lukas Brenner</h1>
      <p class="holder-role">CEO/Founder</p>
    </div>
    <ul class="contact">
      <li class="address">214 Lindenhof Road</li>
      <li class="address">Suite 3 Westfeld, 5120</li>
      <li><svg viewBox="0 0 24 24"><path d="M6.6 10.8a15 15 0 0 0 6.6 6.6l2.2-2.2a1 1 0 0 1 1-.25 11.4 11.4 0 0 0 3.6.6 1 1 0 0 1 1 1V20a1 1 0 0 1-1 1A17 17 0 0 1 3 4a1 1 0 0 1 1-1h3.5a1 1 0 0 1 1 1c0 1.25.2 2.450.6 3.6a1 1 0 0 1-.25 1z"/></svg>(555) 018 - 2240</li>
      <li><svg viewBox="0 0 24 24"><path d="M2 5h20v14H2z M2 5l10 8 10-8" fill="none" stroke="#fff" stroke-width="2"/></svg>info@kernwerkpersonal.com</li>
      <li><svg viewBox="0 0 24 24"><circle cx="12" cy="12" r="9" fill="none" stroke="#fff" stroke-width="2"/><path d="M3 12h18M12 3c3 3 3 15 0 18M12 3c-3 3-3 15 0 18" fill="none" stroke="#fff" stroke-width="1.5"/></svg>www.kernwerkpersonal.com</li>
    </ul>
    <div class="brand-front">
      <div class="brand-name"><span class="brand-mark"></span>Kernwerk</div>
      <div class="brand-sub">Personalberatung</div>
    </div>
  </section>

  <section class="card card-back" aria-label="Business card back">
    <div class="pattern-field" role="img" aria-label="Repeating brand monogram pattern in tonal blues"></div>
    <div class="brand-back">
      <div class="brand-name"><span class="brand-mark"></span>Kernwerk</div>
      <div class="brand-sub">Personalberatung</div>
    </div>
  </section>
</main>
</body>
</html>
```